Coastline Premier Retreats Business Card Design

Design a business card for Coastline Premier Retreats. Look at the website for colors and reference. Card should have logo, name, title, office number, mobile number, email, URL and a tagline like, "Luxury Hotel & Resort Email Marketing" (This might change).

https://www.coastlinepremierretreats.example

The rest I will leave up to your imagination.

Contact Information for Business Card

Logo, name, title, office number, mobile number, email, URL and a tagline like, "Luxury Hotel & Resort Email Marketing" (This might change).

```html
<!DOCTYPE html>
<html lang="en">
<head>
<meta charset="utf-8">
<title>Coastline Premier Retreats – Business Card</title>
<link rel="stylesheet" href="https://fonts.googleapis.com/css2?family=Montserrat:wght@500;600;700&family=Lato:wght@400&family=Satisfy&display=swap">
<style>
  :root {
    --stage: #2b2b2b;
    --card: #1d1d1e;
    --card-edge: #262627;
    --orange: #f07c1a;
    --white: #f2f2f2;
    --silver: #c9c9c9;
    --grey: #a8a8a8;
    --divider: #4a4a4a;
  }
  * { box-sizing: border-box; margin: 0; padding: 0; }
  html, body { width: 1200px; height: 689px; overflow: hidden; background: var(--stage); }
  .stage {
    position: relative; width: 1200px; height: 689px;
    display: flex; align-items: center; justify-content: center; gap: 50px;
  }
  .card {
    position: relative; width: 525px; height: 300px;
    background: var(--card); border-radius: 16px;
    border: 1px solid var(--card-edge);
  }
  /* Front */
  .card--front { display: flex; flex-direction: column; align-items: center; justify-content: center; gap: 26px; }
  .brand--front {
    font-family: "Montserrat", sans-serif; font-weight: 700;
    font-size: 30px; letter-spacing: 1px; text-transform: uppercase;
    color: var(--silver); text-align: center; line-height: 1.15;
  }
  .tagline {
    font-family: "Satisfy", cursive; font-size: 24px; color: var(--orange);
  }
  /* Back */
  .card--back { display: flex; align-items: center; padding: 0 30px 0 34px; }
  .brand-block { width: 225px; display: flex; align-items: center; gap: 10px; }
  .brand-square { width: 14px; height: 14px; background: var(--orange); flex: none; }
  .brand--back {
    font-family: "Montserrat", sans-serif; font-weight: 700; font-size: 17px;
    text-transform: uppercase; color: var(--white); line-height: 1.2; letter-spacing: .5px;
  }
  .divider { width: 1px; height: 180px; background: var(--divider); margin: 0 22px 0 12px; }
  .contact { flex: 1; }
  .person-name {
    font-family: "Montserrat", sans-serif; font-weight: 600; font-size: 21px;
    color: var(--grey); text-transform: uppercase; letter-spacing: .5px;
  }
  .person-title {
    font-family: "Montserrat", sans-serif; font-weight: 500; font-size: 13px;
    color: var(--orange); margin-bottom: 14px;
  }
  .contact-list { list-style: none; font-family: "Lato", sans-serif; font-size: 11px; color: var(--white); }
  .contact-list li { display: flex; align-items: flex-start; gap: 8px; line-height: 1.45; margin-bottom: 3px; }
  .contact-list svg { width: 11px; height: 11px; flex: none; margin-top: 3px; fill: var(--orange); }
</style>
</head>
<body>
<main class="stage">
  <section class="card card--front" aria-label="Card front">
    <div class="brand--front">Coastline Premier<br>Retreats</div>
    <p class="tagline">Luxury Hotel &amp; Resort Email Marketing</p>
  </section>

  <section class="card card--back" aria-label="Card back">
    <div class="brand-block">
      <span class="brand-square"></span>
      <div class="brand--back">Coastline Premier Retreats</div>
    </div>
    <div class="divider"></div>
    <div class="contact">
      <h1 class="person-name">Daniel Harper</h1>
      <p class="person-title">Founder &amp; CEO</p>
      <ul class="contact-list">
        <li>
          <svg viewBox="0 0 12 12"><path d="M6 0a4 4 0 0 0-4 4c0 3 4 8 4 8s4-5 4-8a4 4 0 0 0-4-4zm0 5.6A1.6 1.6 0 1 1 6 2.4a1.6 1.6 0 0 1 0 3.2z"/></svg>
          <span>4870 Harbor Crest Lane<br>Mystic, CT 06355</span>
        </li>
        <li>
          <svg viewBox="0 0 12 12"><path d="M2.4 0.6l2 2.2-1 1.4c.7 1.6 2 2.9 3.5 3.6l1.4-1 2.2 2-1 2.2C5 10.8 1.2 7 .4 1.6z"/></svg>
          <span>(555) 014-2280</span>
        </li>
        <li>
          <svg viewBox="0 0 12 12"><path d="M3 0h6v12H3zM4 1.5v8h4v-8zM5.5 10.3h1v.9h-1z" fill-rule="evenodd"/></svg>
          <span>(555) 014-3391</span>
        </li>
        <li>
          <svg viewBox="0 0 12 12"><path d="M0 2h12v8H0zM0.8 2.6L6 6.6l5.2-4v.9L6 7.6.8 3.5z"/></svg>
          <span>info@coastlinepremierretreats.example</span>
        </li>
        <li>
          <svg viewBox="0 0 12 12"><circle cx="6" cy="6" r="5.5"/><path d="M0.5 6h11M6 .5c2 2 2 9 0 11M6 .5c-2 2-2 9 0 11" stroke="#1d1d1e" stroke-width=".8" fill="none"/></svg>
          <span>coastlinepremierretreats.example</span>
        </li>
      </ul>
    </div>
  </section>
</main>
</body>
</html>
```